KVOR Individual and Corporate Development Business Card Design

KVOR needs a business card design that is aligned with it's values and targetted markets. Coherent Lattice of Adaptive Reasoning Method's self diagnosis model and tools, which can be used for personal improvement and team/business performance enhancement, is based on the learnings of over 20 years of medical practitioning. KVOR supercharges personal effectiveness and awareness to also increase team and business performance.

The targetted markets are high performance individuals and teams who aspire seek to enhance their capabilities and achieve their absolute best potential.

Look and feel for the business card design we are looking for is high technology, premium, fresh, new and medical.

Target Market(s)

Industry/Entity Type

Business Consultant

Contact Information for Business Card

Logo, Full Name, Title, Phone number, Email, company name, Address,

Font styles to use
Sans Serif

Requirements
Must have
• Tag line: Maximising Performance for Highly Effective People
• Please use same colours as the logo.

```html
<!DOCTYPE html>
<html lang="en">
<head>
<meta charset="utf-8">
<title>KVOR Business Card</title>
<link rel="stylesheet" href="https://fonts.googleapis.com/css2?family=Exo+2:wght@400;500;600;700&display=swap">
<style>
  :root {
    --page-bg: #e7e4df;
    --teal-light: #2497ad;
    --teal-dark: #0c6a85;
    --silver-light: #eceeee;
    --silver-dark: #c9cdce;
    --band: #2b2624;
    --brand: #17707f;
    --brand-deep: #1b3f4a;
    --text-light: #f2f6f7;
    --text-soft: #d6e6ea;
    --web-text: #cbbfb8;
  }
  * { margin: 0; padding: 0; box-sizing: border-box; }
  html, body { width: 1200px; height: 970px; overflow: hidden; }
  body {
    background: var(--page-bg);
    font-family: "Exo 2", sans-serif;
    position: relative;
  }
  .card {
    position: absolute;
    left: 100px; top: 200px;
    width: 1000px; height: 570px;
    border-radius: 28px;
    overflow: hidden;
    box-shadow: 0 12px 40px rgba(0,0,0,0.18);
  }
  .card-shapes { position: absolute; inset: 0; }
  .card-text { position: absolute; color: var(--text-light); }
  .holder-name { left: 48px; top: 84px; font-size: 30px; font-weight: 500; letter-spacing: 0.5px; }
  .holder-title { left: 48px; top: 120px; font-size: 22px; font-weight: 400; color: var(--text-soft); }
  .divider { position: absolute; left: 48px; width: 352px; height: 2px; background: var(--text-soft); }
  .divider.top { top: 200px; }
  .divider.bottom { top: 394px; }
  .address { left: 48px; top: 224px; font-size: 22px; line-height: 32px; }
  .contact-row { left: 48px; display: flex; align-items: center; gap: 12px; font-size: 23px; }
  .contact-row.phone { top: 312px; }
  .contact-row.email { top: 347px; font-size: 22px; }
  .contact-row svg { width: 26px; height: 26px; flex: none; }
  .tagline { left: 52px; top: 424px; font-size: 22px; line-height: 32px; letter-spacing: 2px; color: var(--text-soft); }
  .brand-name {
    position: absolute; left: 580px; top: 118px; width: 380px;
    font-size: 96px; font-weight: 700; color: var(--brand);
    letter-spacing: 4px; line-height: 1; text-align: center;
  }
  .brand-rule { position: absolute; left: 548px; top: 225px; width: 424px; height: 2px; background: #8fa4a8; }
  .brand-descriptor {
    position: absolute; left: 548px; top: 236px; width: 424px;
    font-size: 20px; font-weight: 600; color: var(--brand-deep);
    line-height: 26px; text-align: center; letter-spacing: 0.3px;
  }
  .web-address {
    position: absolute; left: 640px; top: 460px; width: 360px;
    text-align: center; font-size: 21px; color: var(--web-text); letter-spacing: 1px;
  }
</style>
</head>
<body>
  <div class="card">
    <svg class="card-shapes" viewBox="0 0 1000 570" width="1000" height="570">
      <defs>
        <linearGradient id="silverFill" x1="0" y1="0" x2="1" y2="1">
          <stop offset="0" stop-color="var(--silver-light)"/>
          <stop offset="1" stop-color="var(--silver-dark)"/>
        </linearGradient>
        <linearGradient id="tealFill" x1="0" y1="0" x2="0.6" y2="1">
          <stop offset="0" stop-color="var(--teal-light)"/>
          <stop offset="1" stop-color="var(--teal-dark)"/>
        </linearGradient>
      </defs>
      <rect class="panel-silver" x="0" y="0" width="1000" height="570" fill="url(#silverFill)"/>
      <polygon class="web-band" points="548,440 1000,440 1000,505 575,505" fill="var(--band)"/>
      <polygon class="panel-teal" points="0,0 388,0 625,570 0,570" fill="url(#tealFill)"/>
    </svg>

    <div class="card-text holder-name">LIAM CARVER</div>
    <div class="card-text holder-title">Founder</div>
    <div class="divider top"></div>
    <div class="card-text address">PO BOX 458 Harlow Lane<br>3rd street Ballarat</div>
    <div class="card-text contact-row phone">
      <svg viewBox="0 0 26 26" aria-hidden="true"><circle cx="13" cy="13" r="11.5" fill="none" stroke="currentColor" stroke-width="1.5"/><rect x="9" y="6.5" width="8" height="13" rx="1.5" fill="none" stroke="currentColor" stroke-width="1.5"/><line x1="12" y1="17" x2="14" y2="17" stroke="currentColor" stroke-width="1.5"/></svg>
      <span>(555) 014-2378</span>
    </div>
    <div class="card-text contact-row email">
      <svg viewBox="0 0 26 26" aria-hidden="true"><circle cx="13" cy="13" r="11.5" fill="none" stroke="currentColor" stroke-width="1.5"/><rect x="7" y="9" width="12" height="8.5" fill="none" stroke="currentColor" stroke-width="1.5"/><polyline points="7,9 13,14 19,9" fill="none" stroke="currentColor" stroke-width="1.5"/></svg>
      <span>info@kvorgroup.com</span>
    </div>
    <div class="divider bottom"></div>
    <div class="card-text tagline">Maximising Performance<br>for Highly Effective People</div>

    <div class="brand-name">KVOR</div>
    <div class="brand-rule"></div>
    <div class="brand-descriptor">COHERENT LATTICE OF ADAPTIVE<br>REASONING METHOD</div>

    <div class="web-address">www.kvorgroup.com</div>
  </div>
</body>
</html>
```